Cover for Lanterns Along the Quiet Shore of Being

Cover for a book that describes everything that happens to a person, from pre-birth life plans through growing in compassion and wisdom to death and living in the afterlife. The information is revealed in messages from people living in the life after this life. The title is Lessons Gathered From Every Season of Your Existence: Shared by Voices Dwelling Beyond the Veil. Author is T. Wesley Prandt. Book size is 6 by 9.

Target Market(s)

General

Font styles to use
Serif

```html
<!DOCTYPE html>
<html lang="en">
<head>
<meta charset="utf-8">
<title>Lanterns Along the Quiet Shore of Being — Book Cover</title>
<link rel="stylesheet" href="https://fonts.googleapis.com/css2?family=Cinzel:wght@400&family=Marcellus&family=Lato:wght@300;400&display=swap">
<style>
  :root {
    --page-bg: #ffffff;
    --sky-top: #a8d3d6;
    --glow: #eef9f8;
    --water-mid: #6fa6ac;
    --water-deep: #1f3f45;
    --water-black: #040708;
    --ink: #0b1417;
    --subtitle-ink: #f2f6f6;
    --author-ink: #b9e3e6;
  }
  * { margin: 0; padding: 0; box-sizing: border-box; }
  html, body {
    width: 1200px;
    height: 1000px;
    overflow: hidden;
    background: var(--page-bg);
  }
  .canvas {
    position: relative;
    width: 1200px;
    height: 1000px;
  }
  .book-cover {
    position: absolute;
    left: 295px;
    top: 38px;
    width: 610px;
    height: 917px;
    overflow: hidden;
  }
  .cover-photo {
    position: absolute;
    inset: 0;
    background:
      radial-gradient(ellipse 300px 170px at 50% 255px, var(--glow) 0%, rgba(238,249,248,0.6) 45%, rgba(238,249,248,0) 100%),
      linear-gradient(180deg,
        var(--sky-top) 0%,
        #a3cfd3 30%,
        #8fbfc4 45%,
        var(--water-mid) 55%,
        #3f7078 66%,
        var(--water-deep) 76%,
        #0c1a1d 86%,
        var(--water-black) 100%);
  }
  .title-block {
    position: absolute;
    left: 0;
    right: 0;
    top: 88px;
    text-align: center;
    color: var(--ink);
  }
  .title-lead {
    font-family: "Marcellus", serif;
    font-size: 25px;
    letter-spacing: 0.01em;
    line-height: 1;
  }
  .title-main {
    margin-top: 16px;
    font-family: "Cinzel", serif;
    font-weight: 400;
    font-size: 62px;
    line-height: 80px;
    letter-spacing: 0.005em;
  }
  .title-main .line { display: block; }
  .subtitle {
    position: absolute;
    left: 0;
    right: 0;
    top: 808px;
    text-align: center;
    font-family: "Marcellus", serif;
    font-size: 15px;
    color: var(--subtitle-ink);
    letter-spacing: 0.02em;
  }
  .author {
    position: absolute;
    left: 0;
    right: 0;
    top: 862px;
    text-align: center;
    font-family: "Lato", sans-serif;
    font-weight: 300;
    font-size: 29px;
    letter-spacing: 0.32em;
    color: var(--author-ink);
    padding-left: 0.32em;
  }
</style>
</head>
<body>
  <div class="canvas">
    <section class="book-cover">
      <div class="cover-photo" role="img" aria-label="Photograph of a single water drop falling into still teal water, with circular ripples spreading across a surface that fades to black"></div>

      <header class="title-block">
        <p class="title-lead">Lessons Gathered From</p>
        <h1 class="title-main">
          <span class="line">Every Season</span>
          <span class="line">of Your</span>
          <span class="line">Existence</span>
        </h1>
      </header>

      <p class="subtitle">Shared by Voices Dwelling Beyond the Veil.</p>
      <p class="author">T. WESLEY PRANDT</p>
    </section>
  </div>
</body>
</html>
```